SaaS / Consulting / Solution website redesign

We need a website design that:
- Is completely different than our current design : https://plumvessel.net
- Has a very minimal amount of copy
- Changes our positioning from a SaaS application to a solutions company. Solutions company means that we help our customers solve their problems with consulting, training, and tools. An example of a solutions company is here: https://oldpages.example/web/20130111103320/http://www.brindlework.com:80/
- Does not make us look like a start up
- Is more people oriented than technology oriented

We need a designer that:
- Is a rebel at heart
- Is a minimalist
- Tells us why our current site sucks
- Can disagree with us
- Can also do copywriting or already has a copywriter that can help
- Is ok with saying we have capability that we don't in order to see if people actually want that
- Can understand the difference between our grand vision and where we need to focus ourselves today in order to get there

Who we are:
- Entrepreneurs
- Programmers
- Consultants
- Investors

Here's our design goals:
#1 Get customers, investors, employers, and partners excited about our unique and clearly articulated value proposition
#2 Get people to contact us asking for help with their programs
#3 Position ourselves as an expert in the skills based volunteering, mentorship, and group collaboration
#4 Make it easy for people, who already know who we are, to register online

What our grand vision is:
- Create a marketplace where any person can go to our site and find time with anyone they need to meet with. Whether that is their hair stylist, school advisor, parent of your kids class, dentist, attorney, etc.

What will you get if you win:
- In addition to the prize of this project we will have many landing pages and other revisions we will need in the future. We currently don't have a designer or copywriter and need to add that capability to our team

Who do we need to appeal to:
- Directors that are launching innovative programs inside organizations
- IT personnel who are trying to disqualify our technology so they don't have to support it or deal with it when it doesn't go well
- Enterprise IT architects who don't want our product being on its own island within their organization totally incompatible with everything else. Architects which are trying to assess how our platform will co-exist with all their other platforms
- Vice Presidents who want to help their directors understand that we don't have enough experience to help them
- Program managers who have to juggle a million things and need a tool that actually helps instead of confuses them and adds more work for them.
- Program managers & directors that have been given ambiguous goals by their board of directors like "improve retention, increase engagement, create innovation, get people to collaborate." And who have no idea where to start or how to deliver on things like that.
- Program managers, directors, and vice presidents that are trying to understand how our technology and services fit into their existing technology and capability
- Employees who are bored and uninspired with their current tools and are hoping for some excitement in their life. Kind of like candy or a double espresso.
- Investors who think, our company like all the rest, are going to waste their money and make them look like a fool

Other information:
-The CSS and html needs to be responsive

-Our registration onboarding flow needs to collect this information:
User first name
user last name
user email
(verify their email)
user phone number
(verify their phone number)
User profile image (optional)
User profile summary (optional, like a bio, freeform text fiels)
If applicable: Register their organization
Organization name
Organization image (optional)
Account Mailing address
account Billing address (could be same as mailing address)
account Billing email address (could be same as user address)
account Product selection (pricing tier)
account Credit card information

The designs I am getting are a good start but they are only the front page. I just want you to know that I am expecting and need more than a landing page to complete the design. I will likely need a page that outlines the benefits and features of the product itself, how its different than our competitors, which will not be on the front page. I will need a registration flow. I will need a blog page design so we can post blog articles, I will need a team page, a page that goes into detail on our training, our services. I will likely need a page that shows all news and media we have been in. I need to show customer and user quotes, case studies, a way to contact us, partners, general resources like on collaboration, product tutorials, customers. I need the site to address a comprehensive set of needs. I need that design to be consistent and thorough. I know what PlateHarbor is. I'm not using because I need more than a template that was customized. I need to be unique and match our brand thoughtfully, beautifully, and artistically. Someone asked me a question about how Murmly is similar to our tool in the way it is referred by end users and purchased by managers. Our website needs to primarily talk to the managers as I explained in the brief but it needs to appear cool and exciting to our end-users without focusing on the technology too much. Murmly is a tool that teams use to collaborate in small and large enterprises. The value prop for them is that communication is easier. But they don't put that on their website. Why? Because the users of the technology won't go to the website to find out information on it, they get their information from someone who is using it and demos it to them. When Ines tells her manager Otto "Lets get murmly, Ruth is using it at her company and its great" Ines's manager doesn't know anything about murmly so she promptly googles it. The most important thing from Ines's perspective is that Otto agrees to try it out. Otto's biggest concern is that productivity will be enhanced to degraded. Murmly knows this and so on the front page they know they are talking to Otto NOT Ines because Ines is already sold on it and doesn't need to get sold on the website. Ines is end user. Otto is the purchaser. We have the same problem and so our end users are not the ones purchasing our product, their managers are purchasing our product. We get referred by our end users and vetted by their managers. Hope this helps! Thank you for looking at this project!  Added Wednesday, June 7, 2017

Another observation I am having about the designs being submitted. I believe we used the animations on our current website because animations / cartoons connect with the "inner child" in our users. Whatever that means :-). I think it's what makes our brand fun. I have a hard time imagining that we could make the design fun looking without animations but I'm sure it can be achieved. I also recognize that blending pictures of real people and animations is hard. So either we must masterfully blend them, use only animations, or make the real people have a LOT of fun! So far most of the designs while achieve the goal of appealing to the serious Vice Presidents and directors, they are not doing a good job at appealing to the overworked program managers and bored employees. There seems to stand another challenge with animations which is animations are hard to find and/or create that achieve the message / emotion we are trying to communicate. I don't have any good answers for this but I will say we can hire both animators and illustrators if we need to. All you have to do is communicate the effect in the website design with some simpler version maybe not the end illustration or animation itself. Added Wednesday, June 7, 2017

• Sex appeal and a sense of humor. Copy that makes people excited and clairvoyant about our potential.
• Boring renditions of other non-inspiring websites

```html
<!DOCTYPE html>
<html lang="en">
<head>
<meta charset="utf-8">
<title>Plumvessel — Face-to-face engagement</title>
<link href="https://fonts.googleapis.com/css2?family=Montserrat:wght@300;400;500;600&display=swap" rel="stylesheet">
<style>
:root{
  --blue:#3daee6;
  --green:#8ccf7e;
  --green-dark:#76c068;
  --ink:#2b2f33;
  --muted:#6b7278;
  --footer:#4c5d67;
  --hero-a:#2f6f80;
  --hero-b:#6d9aa3;
  --white:#ffffff;
  --line:#e4e8ea;
}
*{box-sizing:border-box;margin:0;padding:0}
html,body{width:1200px;height:3109px;overflow:hidden}
body{font-family:"Montserrat",Arial,sans-serif;color:var(--ink);background:var(--white);position:relative}
section,header,footer{position:relative;width:1200px;overflow:hidden}
.btn{display:inline-block;border-radius:22px;color:var(--white);font-size:12px;font-weight:500;text-align:center;text-decoration:none}
.btn-green{background:var(--green);border:3px solid rgba(255,255,255,.7)}
.btn-blue{background:var(--blue);border:3px solid var(--white)}
.brand{display:flex;align-items:center;gap:10px;font-weight:500;font-size:26px;color:var(--green)}
.brand-dot{width:34px;height:34px;border-radius:50%;border:4px solid var(--green)}

/* Hero */
.hero{height:560px}
.hero-bg{position:absolute;inset:0;background:linear-gradient(100deg,var(--hero-a) 0%,#4e8792 45%,var(--hero-b) 75%,#5c8d98 100%)}
.hero .brand{position:absolute;left:160px;top:24px}
.topbar{position:absolute;right:150px;top:28px;display:flex;gap:28px;font-size:12px;color:var(--white)}
.topbar .call{color:var(--green)}
.nav{position:absolute;left:448px;top:76px;display:flex;gap:30px;font-size:12px;color:var(--white)}
.nav .active{color:var(--blue)}
.hero h1{position:absolute;top:150px;width:100%;text-align:center;font-weight:300;font-size:38px;line-height:46px;color:var(--white)}
.laptop{position:absolute;left:288px;top:290px;width:624px;height:270px;background:#dfe3e5;border-radius:18px 18px 0 0;padding:14px 14px 0}
.screen{width:100%;height:100%;background:var(--white);position:relative;overflow:hidden}
.screen .side{position:absolute;left:0;top:26px;bottom:0;width:76px;background:#2f7d8c}
.screen .top{position:absolute;left:0;right:0;top:0;height:26px;border-bottom:1px solid var(--line);font-size:8px;color:var(--green);padding:8px 10px}
.stat{position:absolute;top:34px;width:108px;height:42px;background:var(--white);box-shadow:0 1px 3px rgba(0,0,0,.15);display:flex}
.stat i{width:42px;height:42px;display:block}
.stat b{font-size:12px;font-weight:400;color:#9aa;padding:8px}
.chart{position:absolute;left:86px;top:90px;width:300px;height:160px;border:1px solid var(--line)}

/* Pitch band */
.pitch{height:120px;background:var(--blue);color:var(--white)}
.pitch p{position:absolute;left:155px;top:30px;font-size:12px;line-height:18px;width:420px}
.pitch p strong{font-size:15px;font-weight:600}
.pitch .btn{position:absolute;left:838px;top:34px;width:210px;height:50px;line-height:44px;font-size:13px}

/* Program design */
.program{height:412px;text-align:center}
.section-title{font-size:22px;font-weight:500;color:var(--ink)}
.section-sub{font-size:11px;color:var(--blue);margin-top:6px}
.program .head{position:absolute;top:60px;width:100%}
.features{position:absolute;top:148px;left:130px;width:940px;display:flex;justify-content:space-between}
.feature{width:230px;font-size:12px;line-height:17px;color:var(--ink)}
.feature svg{display:block;margin:0 auto 20px}
.program .btn{position:absolute;left:532px;top:312px;width:136px;height:36px;line-height:34px;border:0;font-size:11px}

/* Split panels */
.panels{height:358px;display:flex}
.panel{width:600px;height:358px;position:relative;color:var(--white)}
.panel-left .photo{position:absolute;inset:0;background:linear-gradient(160deg,#5d8894,#2f5c68 60%,#3d6b76)}
.panel-right .photo{position:absolute;inset:0;background:linear-gradient(160deg,#767f85,#4a5a63 55%,#5f6d74)}
.panel h3{position:absolute;font-size:20px;font-weight:500}
.panel p{position:absolute;font-size:11px;line-height:15px;width:450px}
.panel-left h3{left:64px;top:214px}
.panel-left p{left:64px;top:252px}
.panel-right h3{left:65px;top:136px}
.panel-right p{left:65px;top:170px;width:460px}
.panel .btn{position:absolute;left:65px;top:228px;width:138px;height:34px;line-height:34px;background:var(--green);font-size:11px}

/* Testimonial */
.testimonial{height:458px;text-align:center}
.testimonial .quote-icon{position:absolute;left:582px;top:70px}
.testimonial blockquote{position:absolute;top:130px;left:220px;width:760px;font-size:17px;line-height:28px;color:var(--muted);font-weight:300}
.testimonial blockquote .mark{color:var(--blue);font-weight:600}
.avatars{position:absolute;top:268px;left:0;width:100%;display:flex;justify-content:center;align-items:center;gap:20px}
.avatar{border-radius:50%;background:linear-gradient(#c9cdd0,#9aa0a4)}
.avatar.sm{width:58px;height:58px}
.avatar.lg{width:78px;height:78px;background:linear-gradient(#d8d0c8,#8c8f92);border:3px solid var(--white);box-shadow:0 2px 6px rgba(0,0,0,.2)}
.arrow-l,.arrow-r{font-size:22px;color:#c8ccce}
.arrow-r{color:var(--green)}
.person{position:absolute;top:364px;width:100%}
.person .name{font-size:13px;font-weight:600;letter-spacing:2px}
.person .role{font-size:11px;color:var(--muted);margin-top:4px}
.person .role span{color:var(--blue)}

/* Consulting */
.consulting{height:305px;background:var(--blue);color:var(--white)}
.consulting h2{position:absolute;left:155px;top:62px;font-size:22px;font-weight:500}
.consulting p{position:absolute;left:155px;top:104px;width:560px;font-size:12px;line-height:18px}
.consulting .offer{top:152px;font-weight:600}
.consulting .btn{position:absolute;left:155px;top:200px;width:138px;height:38px;line-height:32px;border:3px solid rgba(255,255,255,.75)}
.consulting .art{position:absolute;left:745px;top:30px;width:455px;height:275px;background:linear-gradient(160deg,rgba(255,255,255,.12),rgba(240,110,60,.55) 70%,rgba(240,110,60,.8));clip-path:polygon(0 78%,40% 40%,62% 58%,100% 10%,100% 100%,0 100%)}

/* Experience */
.experience{height:311px;text-align:center}
.experience .head{position:absolute;top:66px;width:100%}
.clients{position:absolute;top:166px;left:150px;width:900px;display:flex;justify-content:space-between;align-items:center}
.client{display:flex;align-items:center;gap:8px;font-size:20px;font-weight:600;color:#4d5a62}
.client i{width:22px;height:22px;border-radius:50%;background:#4d5a62;display:block}

/* CTA */
.cta{height:298px;background:var(--green);text-align:center}
.cta h2{position:absolute;top:74px;width:100%;font-size:36px;line-height:46px;font-weight:300;color:var(--white)}
.cta .btn{position:absolute;left:494px;top:184px;width:212px;height:52px;line-height:46px;font-size:13px}
.to-top{position:absolute;right:50px;top:250px}

/* Footer */
.site-footer{height:287px;background:var(--footer);color:#d5dde1;font-size:12px;line-height:21px}
.site-footer .brand{position:absolute;left:160px;top:58px}
.copyright{position:absolute;left:157px;top:108px;font-size:11px;line-height:15px}
.fcol{position:absolute;top:62px;list-style:none}
.fcol .active{color:var(--blue)}
.col1{left:383px}.col2{left:611px}
.contact{position:absolute;left:839px;top:62px;font-size:11px;line-height:15px}
.contact .phone{font-size:18px;margin-top:6px;line-height:22px}
.social{position:absolute;left:1122px;top:78px;display:flex;flex-direction:column;gap:14px}
.social i{display:block;width:26px;height:26px;border-radius:50%;border:2px solid #d5dde1}
.social i.on{border-color:var(--blue)}
</style>
</head>
<body>

<header class="hero">
  <div class="hero-bg" role="img" aria-label="Photo of smiling colleagues meeting in an office, blue-teal tint"></div>
  <div class="brand"><span class="brand-dot"></span>Plumvessel</div>
  <div class="topbar"><span class="call">Call us at 1-800-555-0199</span><span>&#128274; Login</span></div>
  <nav class="nav">
    <span class="active">Company</span><span>Products</span><span>Solutions</span><span>Services &amp; Support</span><span>Industries</span><span>Contact Us</span>
  </nav>
  <h1>Increase face-to-face engagement in<br>your communities &amp; groups</h1>
  <div class="laptop">
    <div class="screen">
      <div class="top">Plumvessel</div>
      <div class="side"></div>
      <div class="stat" style="left:86px"><i style="background:#5cb85c"></i><b>1,075</b></div>
      <div class="stat" style="left:204px"><i style="background:var(--blue)"></i><b>830</b></div>
      <div class="stat" style="left:322px"><i style="background:#f3d23f"></i><b>6,830</b></div>
      <div class="stat" style="left:440px"><i style="background:#4cc08a"></i><b>803</b></div>
      <svg class="chart" viewBox="0 0 300 160">
        <text x="8" y="14" font-size="7" fill="#999" font-family="Montserrat, sans-serif">Monthly active users</text>
        <g stroke="#eef0f1"><line x1="20" y1="40" x2="292" y2="40"/><line x1="20" y1="70" x2="292" y2="70"/><line x1="20" y1="100" x2="292" y2="100"/><line x1="20" y1="130" x2="292" y2="130"/></g>
        <g fill="#b9bcc6">
          <rect x="30" y="96" width="11" height="50"/><rect x="51" y="84" width="11" height="62"/><rect x="72" y="92" width="11" height="54"/>
          <rect x="93" y="88" width="11" height="58"/><rect x="114" y="100" width="11" height="46"/><rect x="135" y="86" width="11" height="60"/>
          <rect x="156" y="94" width="11" height="52"/><rect x="177" y="80" width="11" height="66"/><rect x="198" y="90" width="11" height="56"/>
          <rect x="219" y="84" width="11" height="62"/><rect x="240" y="98" width="11" height="48"/><rect x="261" y="138" width="11" height="8"/>
        </g>
      </svg>
    </div>
  </div>
</header>

<section class="pitch">
  <p><strong>You're here because you also believe the</strong><br>most authentic form of <strong style="font-size:12px">engagement</strong> is face-to-face interaction<br>with other people</p>
  <a class="btn btn-green">Schedule Demo</a>
</section>

<section class="program">
  <div class="head"><h2 class="section-title">Program Design</h2><p class="section-sub">Key Components for helping thousands of companies succeed</p></div>
  <div class="features">
    <div class="feature">
      <svg width="64" height="64" viewBox="0 0 64 64" fill="none" stroke="#3daee6" stroke-width="2"><rect x="6" y="8" width="24" height="16" rx="3"/><rect x="34" y="20" width="24" height="16" rx="3"/><path d="M12 24l-2 8 8-8M52 36l2 8-8-8"/><line x1="8" y1="52" x2="56" y2="52"/></svg>
      Focus on face-to-face<br>meetings</div>
    <div class="feature">
      <svg width="64" height="64" viewBox="0 0 64 64" fill="none" stroke="#3daee6" stroke-width="2"><rect x="12" y="8" width="40" height="48" rx="3"/><path d="M20 22l4 4 6-8M20 36l4 4 6-8"/><line x1="34" y1="22" x2="44" y2="22"/><line x1="34" y1="36" x2="44" y2="36"/></svg>
      Roles and responsibilities<br>of mentors &amp; mentees</div>
    <div class="feature">
      <svg width="64" height="64" viewBox="0 0 64 64" fill="none" stroke="#3daee6" stroke-width="2"><circle cx="32" cy="34" r="20"/><path d="M32 22v12l8 6"/><line x1="26" y1="8" x2="38" y2="8"/></svg>
      Durations for selected men-<br>toring types</div>
    <div class="feature">
      <svg width="64" height="64" viewBox="0 0 64 64" fill="none" stroke="#3daee6" stroke-width="2"><rect x="14" y="6" width="36" height="50" rx="3"/><path d="M20 42l8-10 7 6 9-14"/><line x1="20" y1="48" x2="44" y2="48"/></svg>
      Alumni data analysis and<br>segmentation</div>
  </div>
  <a class="btn btn-green">Explore More</a>
</section>

<section class="panels">
  <div class="panel panel-left">
    <div class="photo" role="img" aria-label="Photo of a team laughing together around a table"></div>
    <h3>Engagement Overview</h3>
    <p>Mentors and mentees meet in person, build trust and grow together over time, with every session planned, tracked and easy to repeat.</p>
  </div>
  <div class="panel panel-right">
    <div class="photo" role="img" aria-label="Photo of colleagues in a mentoring session"></div>
    <h3>Mentor Program Management</h3>
    <p>Match people, set goals and keep every program on track, so managers spend their time on people instead of spreadsheets and email.</p>
    <a class="btn">Explore More</a>
  </div>
</section>

<section class="testimonial">
  <svg class="quote-icon" width="36" height="32" viewBox="0 0 36 32" fill="none" stroke="#3daee6" stroke-width="2"><rect x="2" y="2" width="26" height="20" rx="8"/><path d="M10 22l-2 8 8-8"/></svg>
  <blockquote><span class="mark">“</span> Running my ideas by seasoned mentors has proven instrumental to Quillora's progress. Plumvessel lets me quickly schedule these meetings without a headache so I can get back to launching my startup. <span class="mark">”</span></blockquote>
  <div class="avatars">
    <span class="arrow-l">&#8592;</span>
    <div class="avatar sm" role="img" aria-label="Portrait of a customer"></div>
    <div class="avatar lg" role="img" aria-label="Portrait of Dorian Vale"></div>
    <div class="avatar sm" role="img" aria-label="Portrait of a customer"></div>
    <span class="arrow-r">&#8594;</span>
  </div>
  <div class="person"><p class="name">DORIAN VALE</p><p class="role">Founder, <span>Quillora</span></p></div>
</section>

<section class="consulting">
  <h2>Post-training Consulting</h2>
  <p>We will commit to assisting program managers, staff and leadership through day-to-day issues and challenges.</p>
  <p class="offer">Up to 300 free hours in first 365 days</p>
  <a class="btn">Consult Now</a>
  <div class="art" role="img" aria-label="Cartoon team climbing a rising orange arrow, one looking through a telescope"></div>
</section>

<section class="experience">
  <div class="head"><h2 class="section-title">Our Experience</h2><p class="section-sub" style="color:var(--muted)">Advisory program change management</p></div>
  <div class="clients">
    <div class="client"><i></i>Northfield</div>
    <div class="client"><i></i>Kindlewick</div>
    <div class="client"><i></i>Hublab</div>
    <div class="client"><i></i>Forgeworks</div>
    <div class="client"><i></i>Metro Civic</div>
  </div>
</section>

<section class="cta">
  <h2>Increase face-to-face engagement in<br>your communities &amp; groups</h2>
  <a class="btn btn-blue">Schedule Demo</a>
  <svg class="to-top" width="20" height="26" viewBox="0 0 20 26" fill="none" stroke="#fff" stroke-width="2"><path d="M10 24V3M3 10l7-7 7 7"/></svg>
</section>

<footer class="site-footer">
  <div class="brand"><span class="brand-dot"></span>Plumvessel</div>
  <p class="copyright">© 2016 Plumvessel Inc.<br>All rights reserved</p>
  <ul class="fcol col1"><li>Company</li><li class="active">Products</li><li>Solutions</li><li>Services &amp; Support</li><li>Industries</li><li>Blog</li><li>Press</li></ul>
  <ul class="fcol col2"><li>Privacy</li><li>Legal</li><li>Data Transfers</li><li>Contact Us</li><li>Site Map</li></ul>
  <div class="contact">Plumvessel Inc.<br>48 Larkin Row, Eastvale,<br>RI 02900<br><br>Contact Us:<div class="phone">+1-800-555-0199</div>info@plumvessel.net</div>
  <div class="social"><i></i><i class="on"></i><i></i></div>
</footer>

</body>
</html>
```